Lorvex Tilo medical cannibis cultivation company

tag - Tilo rise
Lorvex Tilo medical cannabis cultivation - logo is selected- can we please see bold examples with our selection. We are mainly dealing with medical companies and professionals. We would like to be stand out in the crowd with our designs. Welcome any and all attempts. Thanks

Target Market(s)

Medical and Professional

Industry/Entity Type

Medical And Science

Font styles to use
Sans Serif

Colors

Designer to choose colors to be used in the design.

Requirements
Must have
• Bright colour and be bold- Love the teal and magenta that is currently on the dark background design.
Nice to have
• shading and the 3D affect- The shadowed appearance.
Should not have
• Anything related to illegal activity or un professional manners

```html
<!DOCTYPE html>
<html lang="en">
<head>
<meta charset="utf-8">
<title>Lorvex Tilo — Business Card</title>
<link rel="stylesheet" href="https://fonts.googleapis.com/css2?family=Marcellus&family=Crimson+Text:wght@400;600&display=swap">
<style>
  :root {
    --page: #e9e6e1;
    --card: #050505;
    --teal: #14a9e0;
    --magenta: #9b479c;
    --grey: #9a9a9c;
    --white: #f4f4f4;
  }
  * { box-sizing: border-box; margin: 0; padding: 0; }
  html, body { width: 1200px; height: 1040px; overflow: hidden; background: var(--page); }
  .canvas { position: relative; width: 1200px; height: 1040px; }

  .card {
    position: absolute;
    width: 640px; height: 366px;
    background: var(--card);
    border-radius: 22px;
    box-shadow: 0 18px 40px rgba(0,0,0,0.35), 0 4px 10px rgba(0,0,0,0.25);
    overflow: hidden;
  }
  .card-front { left: 70px; top: 80px; }
  .card-back { left: 490px; top: 590px; }

  .wordmark {
    font-family: "Crimson Text", serif; font-weight: 600;
    color: var(--teal); letter-spacing: 1px; line-height: 1;
  }
  .tagline {
    font-family: "Crimson Text", serif; font-weight: 400;
    color: var(--white); letter-spacing: 1px; line-height: 1;
  }

  .front-brand { position: absolute; left: 36px; top: 66px; width: 320px; }
  .front-brand .wordmark { font-size: 42px; }
  .front-brand .tagline { font-size: 17px; margin-top: 10px; }

  .person { position: absolute; left: 36px; top: 170px; }
  .person-name { font-family: "Marcellus", serif; color: var(--teal); font-size: 24px; letter-spacing: 1px; }
  .person-role { font-family: "Marcellus", serif; color: var(--magenta); font-size: 16px; letter-spacing: 1px; margin-top: 2px; }

  .contact { position: absolute; left: 36px; top: 238px; font-family: "Crimson Text", serif; color: var(--white); font-size: 14px; line-height: 1.35; }
  .contact-line { display: flex; align-items: center; gap: 8px; }
  .contact-line svg { width: 12px; height: 12px; flex: none; }
  .address { margin-bottom: 4px; }

  .brand-symbol-area {
    position: absolute; right: -60px; top: -50px;
    width: 380px; height: 380px; border-radius: 50%;
    background: radial-gradient(circle at 60% 35%, var(--teal) 0%, rgba(20,169,224,0.6) 35%, rgba(155,71,156,0.85) 65%, rgba(155,71,156,0) 72%);
  }

  .back-logo {
    position: absolute; left: 0; right: 0; top: 140px;
    display: flex; flex-direction: column; align-items: center;
  }
  .back-logo .wordmark { font-size: 46px; }
  .back-logo .tagline { font-size: 18px; margin-top: 12px; }
</style>
</head>
<body>
<main class="canvas">
  <section class="card card-front">
    <div class="brand-symbol-area" role="img" aria-label="Brand symbol area in teal and magenta"></div>
    <div class="front-brand">
      <div class="wordmark">Lorvex Tilo</div>
      <div class="tagline">Tilo rise</div>
    </div>
    <div class="person">
      <div class="person-name">MARA QUELL</div>
      <div class="person-role">CEO/FOUNDER</div>
    </div>
    <div class="contact">
      <div class="address">4120 Aldenwick Road<br>Fernhollow, Eastmark 20718</div>
      <div class="contact-line">
        <svg viewBox="0 0 12 12"><path d="M2 1h2.5l1 3-1.5 1a6 6 0 0 0 3 3l1-1.5 3 1V10a1 1 0 0 1-1 1A9 9 0 0 1 1 2a1 1 0 0 1 1-1z" fill="var(--teal)"/></svg>
        555 014 2290
      </div>
      <div class="contact-line">
        <svg viewBox="0 0 12 12"><rect x="0.5" y="2" width="11" height="8" fill="var(--teal)"/><path d="M0.5 2 6 6.5 11.5 2" stroke="var(--card)" fill="none"/></svg>
        mara@lorvextilo.com
      </div>
      <div class="contact-line">
        <svg viewBox="0 0 12 12"><circle cx="6" cy="6" r="5.5" fill="var(--teal)"/><path d="M0.5 6h11M6 0.5c-2.5 3-2.5 8 0 11M6 0.5c2.5 3 2.5 8 0 11" stroke="var(--card)" fill="none" stroke-width="0.8"/></svg>
        www.lorvextilo.com
      </div>
    </div>
  </section>

  <section class="card card-back">
    <div class="back-logo">
      <div class="wordmark">Lorvex Tilo</div>
      <div class="tagline">Tilo rise</div>
    </div>
  </section>
</main>
</body>
</html>
```